established boer goat stud and dorper sheep stud need an updated look

I need a design to promote the boer goat stud and dorper sheep stud, so its clear and simple
Updates

Details for business card design Wirrabel Boers and Dorper Sheep Stud. I would like silhouette animal head or full body of a boer goat (not a dairy breed goat) and Dorper sheep. Contact: Maree Dalton +61 412578304 Sandra Pollock +61 438615027 Mooroopna North Victoria Australia Email: wirrabel5184@mailvane.com

Industry/Entity Type

Agriculture

Contact Information for Business Card

Wirrabel Boers and Dorper Sheep Stud Maree Dalton +61 412578304 Sandra Pollock +61 438615027 wirrabel5184@mailvane.com Tarrawen Victoria Australia

Colors
EE7325
F08F49
F5BC92
FAE3D3
FDF4ED

Requirements
Must have
• My Boer Goats and Dorper Sheep images see my photos

```html
<!DOCTYPE html>
<html lang="en">
<head>
<meta charset="utf-8">
<title>Wirrabel Boers and Dorper Sheep Stud – Business Card</title>
<link href="https://fonts.googleapis.com/css2?family=Arimo:wght@400;700&display=swap" rel="stylesheet">
<style>
  :root {
    --page-bg: #e6e0da;
    --card-frost: #eee9e4;
    --card-frost-deep: #ddd5cd;
    --card-edge: #cfc6bd;
    --band-dark: #111111;
    --band-light: #f4efe9;
    --pasture-green: #5f8f35;
    --pasture-green-light: #7aa84a;
    --pasture-straw: #b08d62;
    --pasture-soil: #8a6a48;
    --herd-brown: #6a3420;
    --herd-rust: #8a4a2a;
    --ink: #262626;
    --ink-soft: #3a3a3a;
  }
  * { margin: 0; padding: 0; box-sizing: border-box; }
  html, body {
    width: 1200px;
    height: 887px;
    overflow: hidden;
    background: var(--page-bg);
    font-family: "Arimo", Arial, sans-serif;
  }
  .canvas {
    position: relative;
    width: 1200px;
    height: 887px;
  }
  .business-card {
    position: absolute;
    left: 100px;
    top: 168px;
    width: 1000px;
    height: 552px;
    border-radius: 20px;
    overflow: hidden;
    background: linear-gradient(160deg, var(--card-frost) 0%, var(--card-frost-deep) 100%);
    box-shadow: 0 0 0 1.5px var(--card-edge), 0 14px 40px rgba(60, 45, 30, 0.18);
  }
  .card-art {
    position: absolute;
    inset: 0;
    width: 100%;
    height: 100%;
  }
  .stud-name {
    position: absolute;
    left: 49px;
    top: 270px;
    color: var(--ink);
    font-size: 19px;
    font-weight: 700;
    letter-spacing: 0.3px;
    white-space: nowrap;
  }
  .contact-block {
    position: absolute;
    left: 49px;
    top: 322px;
    color: var(--ink);
    font-size: 24.5px;
    line-height: 46px;
    letter-spacing: 0.3px;
  }
  .contact-line { white-space: nowrap; }
  .contact-name {
    font-weight: 700;
    text-transform: uppercase;
    color: var(--ink);
  }
  .contact-phone,
  .contact-value { color: var(--ink-soft); }
</style>
</head>
<body>
<div class="canvas">
  <div class="business-card">
    <svg class="card-art" viewBox="0 0 1000 552" xmlns="http://www.w3.org/2000/svg">
      <defs>
        <linearGradient id="paddockTone" x1="0" y1="0" x2="0" y2="1">
          <stop offset="0" stop-color="var(--pasture-green-light)"/>
          <stop offset="0.08" stop-color="var(--pasture-green)"/>
          <stop offset="0.2" stop-color="var(--pasture-straw)"/>
          <stop offset="0.55" stop-color="var(--pasture-soil)"/>
          <stop offset="1" stop-color="var(--pasture-soil)"/>
        </linearGradient>
        <radialGradient id="herdTone" cx="0.62" cy="0.55" r="0.45">
          <stop offset="0" stop-color="var(--herd-brown)" stop-opacity="0.95"/>
          <stop offset="0.6" stop-color="var(--herd-rust)" stop-opacity="0.7"/>
          <stop offset="1" stop-color="var(--herd-rust)" stop-opacity="0"/>
        </radialGradient>
        <linearGradient id="grassEdge" x1="0" y1="0" x2="1" y2="0">
          <stop offset="0.75" stop-color="var(--pasture-green)" stop-opacity="0"/>
          <stop offset="1" stop-color="var(--pasture-green)" stop-opacity="0.85"/>
        </linearGradient>
        <clipPath id="photoArea">
          <path d="M0,0 H1000 V458 C800,478 640,400 520,300 C380,170 220,118 0,140 Z"/>
        </clipPath>
      </defs>
      <g class="herd-photo" role="img"
         aria-label="Photo of brown Boer goats with ear tags standing on straw in a green paddock"
         clip-path="url(#photoArea)">
        <rect width="1000" height="552" fill="url(#paddockTone)"/>
        <rect width="1000" height="552" fill="url(#herdTone)"/>
        <rect width="1000" height="552" fill="url(#grassEdge)"/>
      </g>
      <path class="wave-band-light" fill="none" stroke="var(--band-light)" stroke-width="12"
            d="M0,175 C220,150 380,200 520,330 C640,440 800,495 1000,470"/>
      <path class="wave-band-dark" fill="none" stroke="var(--band-dark)" stroke-width="15"
            d="M0,141 C220,118 380,170 520,300 C640,410 800,478 1000,458"/>
    </svg>
    <p class="stud-name">Wirrabel Boers and Dorper Sheep Stud</p>
    <div class="contact-block">
      <p class="contact-line"><span class="contact-name">Maree Dalton</span> <span class="contact-phone">+61 412578304</span></p>
      <p class="contact-line"><span class="contact-name">Sandra Pollock</span> <span class="contact-phone">+61 438615027</span></p>
      <p class="contact-line">Email : <span class="contact-value">wirrabel5184@mailvane.com</span></p>
      <p class="contact-line">Address : <span class="contact-value">Tarrawen Victoria Australia</span></p>
    </div>
  </div>
</div>
</body>
</html>
```